New Coffee Shop business card

We are opening our new coffee shop and are needing business cards to take with us on February 6th to Atlanta, Ga to a show.

We will be offering the following menu type items:

coffee
teas
espresso
frappes
smoothies

sandwiches
soups
salads
pastries
ice cream

Our shop is in a rural country-side area and we would like to convey that feel in our shop. In addition to the cafe we will also be selling gifts and furniture and other home decor. Much of this merchandise will be rescued, refurbished or repurposed which is also a core value of what we are all about.

We have a company logo we would like incorporated into the design.

We will also provide files that have the elements of the logo which may also be useful in the design of the card.

Since we are not open yet we need one slightly altered version of the card as well as the final product which states "Opening in the summer 2015"

Target Market(s)

moderate to slightly upscale and folksy.

Industry/Entity Type

Coffee Shop

Contact Information for Business Card

Fern Kettle Coffee
name
address
phone number
email

Card

Font styles to use
Sans Serif

Requirements
Must have
• Must include Logo
• Must include information on menu.
• Must include information on our merchandise sales as described inthe project description.
• Color scheme to complement the logo
Nice to have
• The following descriptions
• "We are also selling gifts, furniture, and other home decoration."
• "We rescue, refurbish, and repurpose old furniture so it can live again."

```html
<!DOCTYPE html>
<html lang="en">
<head>
<meta charset="utf-8">
<title>Fern Kettle Coffee – Business Cards</title>
<link rel="stylesheet" href="https://fonts.googleapis.com/css2?family=Jost:wght@400;500&display=swap">
<style>
  :root {
    --bg: #d6d6d6;
    --card-light: #ffffff;
    --card-dark: #0d0b0a;
    --ink: #333131;
    --red: #8e1d24;
    --red-soft: #b52a2f;
    --tan: #c2b49c;
    --light-grey: #a9a39b;
    --pattern-a: #2a2522;
    --pattern-b: #141110;
    --white: #ffffff;
  }
  * { box-sizing: border-box; margin: 0; padding: 0; }
  html, body { width: 1200px; height: 900px; overflow: hidden; }
  body {
    background: var(--bg);
    font-family: "Jost", "Futura", sans-serif;
    position: relative;
  }
  .card {
    position: absolute;
    width: 550px;
    height: 320px;
    background: var(--card-light);
    box-shadow: 0 4px 14px rgba(0,0,0,.25);
    overflow: hidden;
  }
  .card--opening { left: 40px; top: 70px; }
  .card--final { left: 610px; top: 150px; }
  .card--contact { left: 325px; top: 500px; background: var(--card-dark); }

  .menu-row {
    position: absolute;
    display: flex;
    justify-content: space-between;
    font-size: 13px;
    line-height: 1;
    white-space: nowrap;
  }
  .menu-row--top { top: 10px; left: 28px; right: 28px; }
  .menu-row--bottom { bottom: 10px; left: 28px; right: 28px; transform: rotate(180deg); }
  .menu-row--right { right: 8px; top: 32px; bottom: 32px; writing-mode: vertical-rl; }
  .menu-row--left { left: 8px; top: 32px; bottom: 32px; writing-mode: vertical-rl; transform: rotate(180deg); }

  .item--tan { color: var(--tan); }
  .item--red { color: var(--red); }
  .item--ink { color: var(--ink); }
  .card--contact .item--ink { color: var(--light-grey); }
  .card--contact .item--tan { color: #e6dccb; }
  .card--contact .item--red { color: var(--red-soft); }

  .brand {
    position: absolute;
    left: 0; right: 0;
    display: flex;
    flex-direction: column;
    align-items: center;
    gap: 8px;
  }
  .brand__mark {
    border-radius: 50%;
    background: var(--ink);
  }
  .brand__name {
    color: var(--ink);
    font-size: 40px;
    font-weight: 400;
    line-height: 1.05;
    text-align: center;
  }
  .card--opening .brand { top: 34px; }
  .card--opening .brand__mark { width: 104px; height: 104px; }
  .card--final .brand { top: 46px; }
  .card--final .brand__mark { width: 118px; height: 118px; }

  .opening-note {
    position: absolute;
    left: 0; right: 0; top: 244px;
    text-align: center;
    color: var(--red);
    font-size: 23px;
    letter-spacing: .5px;
  }

  .pattern-field {
    position: absolute;
    inset: 0;
    background: radial-gradient(ellipse at center, var(--pattern-b) 30%, var(--pattern-a) 100%);
  }
  .contact {
    position: absolute;
    left: 190px; top: 92px;
    color: var(--white);
  }
  .contact__name { font-size: 31px; margin-bottom: 18px; margin-left: 8px; }
  .contact__phone { font-size: 20px; letter-spacing: .5px; }
  .contact__address { font-size: 14px; line-height: 1.25; margin-left: -8px; }
  .contact__email { font-size: 16px; color: var(--red-soft); margin-top: 6px; margin-left: 14px; }
</style>
</head>
<body>

<section class="card card--opening">
  <div class="menu-row menu-row--top">
    <span class="item--tan">coffee</span><span class="item--red">tea</span><span class="item--ink">espresso</span><span class="item--tan">frappes</span><span class="item--red">smoothies</span><span class="item--ink">sandwiches</span><span class="item--tan">soups</span><span class="item--red">salads</span>
  </div>
  <div class="menu-row menu-row--right">
    <span class="item--ink">pastries</span><span class="item--red">ice cream</span><span class="item--tan">coffee</span><span class="item--red">tea</span><span class="item--tan">soups</span>
  </div>
  <div class="menu-row menu-row--bottom">
    <span class="item--ink">espresso</span><span class="item--tan">frappes</span><span class="item--red">smoothies</span><span class="item--ink">sandwiches</span><span class="item--tan">soups</span><span class="item--red">salads</span><span class="item--ink">pastries</span>
  </div>
  <div class="menu-row menu-row--left">
    <span class="item--red">ice cream</span><span class="item--tan">coffee</span><span class="item--red">tea</span><span class="item--tan">espresso</span><span class="item--ink">soups</span>
  </div>
  <div class="brand">
    <span class="brand__mark"></span>
    <span class="brand__name">Fern Kettle</span>
  </div>
  <p class="opening-note">OPENING IN THE SUMMER 2015</p>
</section>

<section class="card card--final">
  <div class="menu-row menu-row--top">
    <span class="item--tan">coffee</span><span class="item--red">tea</span><span class="item--ink">espresso</span><span class="item--tan">frappes</span><span class="item--red">smoothies</span><span class="item--ink">sandwiches</span><span class="item--tan">soups</span><span class="item--red">salads</span>
  </div>
  <div class="menu-row menu-row--right">
    <span class="item--ink">pastries</span><span class="item--red">ice cream</span><span class="item--tan">coffee</span><span class="item--red">tea</span><span class="item--tan">soups</span>
  </div>
  <div class="menu-row menu-row--bottom">
    <span class="item--ink">espresso</span><span class="item--tan">frappes</span><span class="item--red">smoothies</span><span class="item--ink">sandwiches</span><span class="item--tan">soups</span><span class="item--red">salads</span><span class="item--ink">pastries</span>
  </div>
  <div class="menu-row menu-row--left">
    <span class="item--red">ice cream</span><span class="item--tan">coffee</span><span class="item--red">tea</span><span class="item--tan">espresso</span><span class="item--ink">soups</span>
  </div>
  <div class="brand">
    <span class="brand__mark"></span>
    <span class="brand__name">Fern Kettle<br>Coffee</span>
  </div>
</section>

<section class="card card--contact">
  <div class="pattern-field" role="img" aria-label="Faint repeating pattern of hunting dogs, birds and steaming coffee cups"></div>
  <div class="menu-row menu-row--top">
    <span class="item--tan">coffee</span><span class="item--red">tea</span><span class="item--ink">espresso</span><span class="item--tan">frappes</span><span class="item--red">smoothies</span><span class="item--ink">sandwiches</span><span class="item--tan">soups</span><span class="item--red">salads</span>
  </div>
  <div class="menu-row menu-row--right">
    <span class="item--ink">pastries</span><span class="item--red">ice cream</span><span class="item--tan">coffee</span><span class="item--red">tea</span><span class="item--tan">soups</span>
  </div>
  <div class="menu-row menu-row--bottom">
    <span class="item--ink">espresso</span><span class="item--tan">frappes</span><span class="item--red">smoothies</span><span class="item--ink">sandwiches</span><span class="item--tan">soups</span><span class="item--red">salads</span><span class="item--ink">pastries</span>
  </div>
  <div class="menu-row menu-row--left">
    <span class="item--red">ice cream</span><span class="item--tan">coffee</span><span class="item--red">tea</span><span class="item--tan">espresso</span><span class="item--ink">soups</span>
  </div>
  <div class="contact">
    <p class="contact__name">Dana Moreau</p>
    <p class="contact__phone">1404 5 210 388</p>
    <p class="contact__address">18 Orchard Lane Ste<br>410. Marietta GA 30060</p>
    <p class="contact__email">moreau@fk.com</p>
  </div>
</section>

</body>
</html>
```